Blood Testing Health App

We are looking for a graphics designer to create a web app for us so that we may insert it into a health management website system.
For branding purposes we are at www.Vantiqor.com and we are revamping our website... Example of new colors attached.
How we work...
We are a blood testing company based in the USA.
We offer a blood testing service nationwide in the USA.
We allow customers to order tests directly from us, visit a lab, have their blood drawn, or submit a urine sample, the lab tests it and they send the results back to our computer system and we share it with the customer.
The benefits of this are the customer does not need to go to the doctor and pay for the doctors visit to order these tests, which save them money. The tests are cheaper than going through the doctor. The customer simply uses us to get the test and the results and they can then take the results to their doctor... this process has saved them money. Others may be interested in regular check ups for blood work etc... and this allows them to do it with out needing a doctor, or if you have no insurance, this is a cheaper option too. We are quicker than a doctor, customers do not need appointments etc.
Hopefully you now have a better understanding as to what we do.
Here is the spec.
The app screen size is 750 px wide by 700 px high. ( A pdf is attached to show where the app is going to go, it is on page 3 of the pdf) The customer will have the ability to scroll… therefore the length of the page can be longer.
The app will consist of the following sections
Entry Page –
This will be the first page the user sees upon opening the app. This will be where they are directed from to the sections of the app discussed below. This needs to be branded for VantiQor with a modern look.
1 – Order Test (Giving them the ability to purchase a blood test within the app)
2 – VantiQor Dashboard (A dashboard that has everything they could need to use our service_
How it works Section on entry page – this will be a simple set of graphics showing how the service works. We already have the graphics for this, they do not need to be built again. They are attached to this brief
Basic structure of sections –
Order Test –
This page contains all tests, filed in categories – and Sub categories – Each test needs a link to an Information section – Price – Buy Now – Cart Process
VantiQor Dashboard –
A page of icons along the top of the app
- My Confirmation
- My Nearest Lab
- My Receipt
- My Orders
- My Account
- My Results
- My Inbox
- Contact Us
Sections in more detail -
Order A Test –
Show all categories/ sub categories – There are 23 categories, 14 sub categories, and within these categories are 300 tests - Here is the information for the categories etc - http://www.vantiqor.com/panels.aspx?PanelGroupID=4 Just in case it helps :)
We need to present this in a graphic format that is spacious, modern (brimlake, kivvo web appearance is the direction we are going for) We need it to be clear and not overwhelming to the customer.
Functionality idea…
Customer clicks category/ subcategory and tests appear.
Customer sees small 35 word description. For more information the test opens into a lightbox or expand the container which ever graphic designer believes to be most visually appealing
Buy Now must always be visible, along with price of the test
Buying process explained – Customer clicks buy now –
They are then taken to a Review Order screen ( This contains Order summary and choose payment method – insert payment details )
– Confirm payment –
Confirmation screen appears, thanking them.
They are then taken to the VantiQor Dashboard...
VantiQor Dashboard –
"My Confirmation" - Print Confirmation Order (PDF is in brief, we want this web based not a pdf download)
"My Nearest Lab Location" - This does not need to be designed because the web developer has this part under control, but we do need the icon in the dashboard
"My Receipt" - Print receipt - This does not exist in our system yet. So we need to create this from scratch - It will need to have - The test they are purchasing and the amount of the test - The customers name - The order ID - Must provide printer friendly option too
"My Orders" - This will have a list of orders - At the end of each order will be a status update of either "Test results" "Open order"
A graphic table format would be perfect. This will be linked to relevant results if they have been received. I have also attached a version of what the customer currently sees on our website. We know it is nasty ;) We are redesigning... but the information is there for this section to help design it with the right info. If the results are ready it will say in this list.
"Results Ready" will be a link to show those results once the customer has clicked the link, and the results will appear in the app, under the icons. There must be a printer friendly version too.
"My Results" Developer will sort this page out but we need the icon... It will be exactly like my orders but only show test results
"My Account" - This will be a place for them to update their personal information - Name, DOB, Address, Email Address
"My Inbox" - An inbox interface - Our way of contacting the customer for promotions we are running etc – We need a design of how this screen will appear. We also need the icon in the dashboard to have a notification on it if there are messages in the customers inbox. A little red 1, or circle with number of messages in the inbox.
"Customer Service" - This does not need to be designed because the web developer has this part under control, but we do need the icon in the dashboard
Icons appear along the top of app ( example - Mac icons/ iphone app icons) When the customer clicks an icon the content always appears below the icons
Here is more information for the icons and what should appear when each icon is clicked.
Screens to be designed –
Entry Page
Order A Test Page
Review Order Screen/Payment Screen - Show a lightbox that shows payment has been confirmed. Customer clicks close and are on the Confirmation Screen
VantiQor Dashboard - Screens mentioned in detail above
We can't wait to see your designs!
Please email any questions.
Hi all this is the first time we have used pixel harbor and understand the budget was too low for this project. We have now increased the budget to $2,000 and extended the deadline by another week
Hi all we are receiving some really great designs. I just added an example of the space that the web app will be going into... It is called "morvelapp.pdf"
Hi guys updated the brief. Hopefully this will help with the dashboard part of the design

```html
<!DOCTYPE html>
<html lang="en">
<head>
<meta charset="utf-8">
<title>VantiQor Dashboard – My Receipts</title>
<link href="https://fonts.googleapis.com/css2?family=Lato:wght@400;700;900&family=Open+Sans:wght@400;600;700&display=swap" rel="stylesheet">
<style>
:root{
  --ink:#2b2b2b;
  --muted:#8a8a8a;
  --green:#7dc142;
  --blue:#1a6fc1;
  --orange:#f25a0f;
  --orange-dark:#d94300;
  --card:#e5e5e5;
  --white:#ffffff;
  --badge:#f0401f;
  --icon:#555555;
}
*{box-sizing:border-box;margin:0;padding:0}
html,body{width:1200px;height:1075px;overflow:hidden;background:var(--white)}
body{position:relative;font-family:"Open Sans",Arial,sans-serif;color:var(--ink)}
.abs{position:absolute}

/* header */
.brand-name{left:29px;top:64px;font-family:"Lato",sans-serif;font-weight:400;font-size:72px;letter-spacing:-1px;color:#333;line-height:1;white-space:nowrap}

.tab{top:46px;width:198px;height:116px;text-align:center;font-family:"Lato",sans-serif;font-size:17px;letter-spacing:.3px}
.tab svg{display:block;margin:22px auto 10px}
.tab-order{left:541px;color:var(--muted)}
.tab-dashboard{left:730px;background:#ececec;border-radius:14px 14px 0 0;color:var(--green)}

.social{top:102px;width:42px;height:42px;border-radius:50%;background:var(--green)}

/* nav band */
.nav{left:0;top:162px;width:1200px;height:216px;background:linear-gradient(#f2f2f2,#dedede)}
.nav-pointer{left:656px;top:364px;width:0;height:0;border-left:14px solid transparent;border-right:14px solid transparent;border-bottom:14px solid var(--white)}
.nav-item{top:46px;width:150px;margin-left:-75px;text-align:center;font-size:18px;line-height:1.05;color:#333}
.nav-icon{display:block;width:100px;height:100px;margin:0 auto 8px;border-radius:50%;
  background:radial-gradient(circle at 50% 35%,#ffffff 0 55%,#d9d9d9 70%,#bdbdbd 100%);
  box-shadow:0 3px 5px rgba(0,0,0,.25);position:relative}
.nav-icon svg{position:absolute;left:25px;top:25px}
.nav-icon.flat{background:radial-gradient(circle at 50% 40%,#7a7a7a 0 32%,#e9e9e9 34%,#cfcfcf 100%)}
.nav-item.active{color:var(--blue)}
.badge{left:96px;top:-14px;width:44px;height:30px;border-radius:8px;background:var(--badge);color:var(--white);font-size:18px;font-weight:700;text-align:center;line-height:30px}

/* receipt card */
.card{left:27px;top:419px;width:1139px;height:514px;background:var(--card);border-radius:16px}
.card-title{left:34px;top:24px;font-family:"Lato",sans-serif;font-weight:900;font-size:38px;color:var(--blue)}
.btn{top:24px;height:35px;border-radius:5px;background:linear-gradient(var(--orange),var(--orange-dark));color:var(--white);font-family:"Lato",sans-serif;font-weight:700;font-size:14px;display:flex;align-items:center;justify-content:center;gap:16px;box-shadow:0 1px 2px rgba(0,0,0,.3)}
.btn i{width:18px;height:18px;border-radius:50%;background:var(--white);display:block;position:relative}
.btn i::after{content:"";position:absolute;left:6px;top:4px;border-left:7px solid var(--orange);border-top:5px solid transparent;border-bottom:5px solid transparent}
.panel{left:26px;top:83px;width:1086px;height:405px;background:var(--white);border-radius:16px}

.meta{font-size:23px;line-height:32px}
.meta-labels{left:0;top:50px;width:158px;text-align:right}
.meta-colons{left:166px;top:50px}
.meta-values{left:203px;top:50px}
.price-head{left:925px;top:74px;font-weight:700;font-size:27px}
.prices{left:880px;top:108px;width:126px;text-align:right;font-size:22px;line-height:31px}
.price-rule{left:899px;top:213px;width:112px;height:1px;background:#666}
.total{left:880px;top:224px;width:126px;text-align:right;font-size:24px;font-weight:700;color:var(--orange)}
</style>
</head>
<body>

<header>
  <div class="abs brand-name">VANTIQOR</div>

  <div class="abs tab tab-order">
    <svg width="52" height="36" viewBox="0 0 52 36"><rect x="6" y="2" width="40" height="26" rx="3" fill="#9a9a9a"/><rect x="1" y="29" width="50" height="5" rx="2" fill="#9a9a9a"/></svg>
    ORDER A TEST
  </div>
  <div class="abs tab tab-dashboard">
    <svg width="40" height="40" viewBox="0 0 40 40"><rect x="12" y="2" width="26" height="24" fill="none" stroke="#7dc142" stroke-width="4"/><rect x="2" y="14" width="26" height="24" fill="#ececec" stroke="#7dc142" stroke-width="4"/></svg>
    DASHBOARD
  </div>

  <span class="abs social" style="left:1005px" aria-label="Social link"></span>
  <span class="abs social" style="left:1067px" aria-label="Social link"></span>
  <span class="abs social" style="left:1128px" aria-label="Social link"></span>
</header>

<nav class="abs nav">
  <div class="abs nav-item" style="left:72px"><span class="nav-icon"><svg width="50" height="50" viewBox="0 0 50 50"><rect x="5" y="6" width="40" height="30" rx="3" fill="none" stroke="#555" stroke-width="4"/><polyline points="10,22 18,22 22,14 28,30 32,22 40,22" fill="none" stroke="#555" stroke-width="3"/><rect x="18" y="38" width="14" height="6" fill="#555"/></svg></span>My<br>Confirmation</div>
  <div class="abs nav-item" style="left:224px"><span class="nav-icon flat" role="img" aria-label="Lab microscope icon"></span>My<br>Nearest Lab</div>
  <div class="abs nav-item" style="left:373px"><span class="nav-icon flat" role="img" aria-label="DNA strand icon"></span>My Orders</div>
  <div class="abs nav-item" style="left:523px"><span class="nav-icon"><svg width="50" height="50" viewBox="0 0 50 50"><rect x="9" y="6" width="32" height="40" rx="3" fill="none" stroke="#555" stroke-width="4"/><polyline points="14,28 20,28 23,20 28,36 31,28 36,28" fill="none" stroke="#555" stroke-width="3"/></svg></span>My Results</div>
  <div class="abs nav-item active" style="left:670px"><span class="nav-icon"><svg width="50" height="50" viewBox="0 0 50 50"><rect x="9" y="6" width="32" height="40" rx="3" fill="none" stroke="#1a6fc1" stroke-width="4"/><rect x="19" y="2" width="12" height="8" rx="2" fill="#1a6fc1"/><g fill="#1a6fc1"><rect x="14" y="16" width="4" height="4"/><rect x="21" y="16" width="15" height="4"/><rect x="14" y="24" width="4" height="4"/><rect x="21" y="24" width="15" height="4"/><rect x="14" y="32" width="4" height="4"/><rect x="21" y="32" width="15" height="4"/></g></svg></span>My Receipts</div>
  <div class="abs nav-item" style="left:818px"><span class="nav-icon flat" role="img" aria-label="Account icon"></span>My Account</div>
  <div class="abs nav-item" style="left:970px"><span class="nav-icon"><svg width="50" height="50" viewBox="0 0 50 50"><rect x="4" y="12" width="42" height="28" fill="#555"/><polyline points="4,12 25,30 46,12" fill="none" stroke="#eee" stroke-width="3"/></svg><span class="abs badge">2</span></span>My Inbox</div>
  <div class="abs nav-item" style="left:1120px"><span class="nav-icon flat" role="img" aria-label="Customer support icon"></span>Contact Us</div>
</nav>
<span class="abs nav-pointer"></span>

<main class="abs card">
  <h1 class="abs card-title">Receipt ID: 0000123</h1>
  <span class="abs btn" style="left:653px;width:120px">PRINT <i></i></span>
  <span class="abs btn" style="left:784px;width:199px">DOWNLOAD PDF <i></i></span>
  <span class="abs btn" style="left:994px;width:118px">EMAIL <i></i></span>

  <section class="abs panel">
    <div class="abs meta meta-labels">Order ID<br>Date<br>Test Name</div>
    <div class="abs meta meta-colons">:<br>:<br>:</div>
    <div class="abs meta meta-values">34584<br>Sept. 20, 2013<br>COMPREHENSIVE Erectile Dysfunction Profile<br>Immunoglobulin G, Subclasses (1-4)<br>Oxcarbazepine, Serum</div>

    <div class="abs price-head">Price</div>
    <div class="abs prices">$75.00<br>$490.00<br>$145.00</div>
    <span class="abs price-rule"></span>
    <div class="abs total">$710.00</div>
  </section>
</main>

</body>
</html>
```